Flyer-Design für psychologische Beratung und Therapie
Zielgruppe
In meiner Praxis für psychologische Beratung und Therapie unterstütze ich Menschen dabei, ihre Probleme zu lösen. Schwerpunkte sind die Stärkung des Selbstwertgefühls, Überwindung von Ängsten und Krisen.
Aufgabenstellung
Din lang 4-Seitig
(Zitat)
'Bei aller Ernsthaftigkeit und Empathie dürfen Leichtigkeit,
Zuversicht und Humor in der Therapie nicht zu kurz kommen.“
(Text)
Mein Name ist Malte Ewald Krings, ich bin Transaktionsanalytiker, psychotherapeutischer Heilpraktiker und begeisterter VIM® Therapeut. Wenn Sie zufriedener leben wollen, neue Wege einschlagen oder sich beruflich oder persönlich weiterentwickeln wollen, begleite ich Sie gern dabei!
Möchten Sie ein stärkeres Selbstwertgefühl entwickeln, Ängste reduzieren oder eine akute Krise überwinden? Oder geeignete Strategien entwickeln, damit Sie Ihren Beruf zufriedener und erfolgreicher ausüben können? Auf dem Weg zu Ihrem Ziel biete ich Ihnen Unterstützung, vereinbaren Sie gerne einen ersten Termin!

```html
<!DOCTYPE html>
<html lang="de">
<head>
<meta charset="utf-8">
<title>Psychologische Beratung und Therapie – Malte Ewald Krings</title>
<link href="https://fonts.googleapis.com/css2?family=Open+Sans:ital,wght@0,400;0,600;0,700;1,400&display=swap" rel="stylesheet">
<style>
  :root {
    --accent: #eea80c;
    --accent-box: #efb10f;
    --quote-dot: #f29a12;
    --text: #585858;
    --rule: #c9c9c9;
    --paper: #ffffff;
    --on-accent: #ffffff;
  }
  * { margin: 0; padding: 0; box-sizing: border-box; }
  html, body { width: 1200px; height: 1200px; overflow: hidden; background: var(--paper); }
  body { font-family: "Open Sans", Arial, sans-serif; color: var(--text); }
  .flyer { position: relative; width: 1200px; height: 1200px; }
  .block { position: absolute; text-align: center; }
  .accent { color: var(--accent); }

  .title {
    left: 40px; width: 524px; top: 42px;
    font-size: 42px; line-height: 49px; font-weight: 600; color: var(--accent);
  }
  .intro {
    left: 40px; width: 524px; top: 174px;
    font-size: 19.5px; line-height: 24.4px;
  }
  .intro p + p { margin-top: 24.4px; }

  .rule { position: absolute; height: 1px; background: var(--rule); }
  .rule-left { left: 73px; width: 458px; top: 535px; }
  .rule-right-1 { left: 677px; width: 457px; top: 224px; }
  .rule-right-2 { left: 679px; width: 458px; top: 526px; }

  .section-heading { font-size: 24px; font-weight: 700; line-height: 30px; }
  .person-heading { left: 40px; width: 524px; top: 580px; }
  .bio {
    left: 50px; width: 504px; top: 648px;
    font-size: 19.5px; line-height: 24.4px; font-weight: 600; color: var(--accent);
  }
  .bio strong { font-weight: 700; }
  .portrait {
    position: absolute; left: 109px; top: 791px; width: 386px; height: 364px;
    background: linear-gradient(180deg, #f4f6f8 0%, #e9edf2 55%, #c9d8ea 100%);
  }

  .quote-mark { position: absolute; left: 660px; top: 52px; }
  .quote {
    left: 700px; width: 410px; top: 64px;
    font-size: 24px; line-height: 29px; font-style: italic; color: var(--accent);
  }
  .services-heading { left: 660px; width: 490px; top: 268px; }
  .services {
    left: 660px; width: 490px; top: 336px; list-style: none;
    font-size: 19.5px; line-height: 28px; font-weight: 600; color: var(--accent);
  }
  .services li + li { margin-top: 12px; }
  .methods-heading { left: 660px; width: 490px; top: 571px; }

  .methods-box {
    position: absolute; left: 651px; top: 644px; width: 513px; height: 511px;
    background: var(--accent-box); color: var(--on-accent);
  }
  .method { position: absolute; top: 20px; width: 224px; text-align: center; }
  .method-ta { left: 22px; }
  .method-vim { left: 258px; }
  .method h3 { font-size: 18px; font-weight: 700; line-height: 22px; height: 36px; }
  .method-ta h3 { padding-top: 2px; }
  .method p { margin-top: 16px; font-size: 18px; line-height: 21.9px; }
  .method-divider { position: absolute; left: 254px; top: 97px; width: 1px; height: 325px; background: var(--on-accent); }
</style>
</head>
<body>
<main class="flyer">
  <h1 class="block title">Psychologische<br>Beratung und Therapie</h1>

  <section class="block intro">
    <p>Wenn Sie <span class="accent">glücklicher und zufriedener</span> leben wollen,<br>neue Wege einschlagen oder sich <span class="accent">beruflich oder<br>persönlich weiterentwickeln</span> wollen, begleite ich Sie<br>gern dabei!</p>
    <p>Wenn Sie unter Ängsten, Phobien, Depressionen lei-<br>den oder eine <span class="accent">Krise bewältigen wollen</span>, ist eine The-<br>rapie mit VIM® geeignet. Erfahrungsgemäß können<br>Sie schon nach den ersten Sitzungen eine <span class="accent">Besserung</span><br>Ihrer Symptome festellen.</p>
    <p>Eine Spezialisierung von mir ist die <span class="accent">Behandlung</span> von<br>Lampenfieber, Auftritts- und Prüfungsangst.</p>
  </section>

  <div class="rule rule-left"></div>

  <h2 class="block section-heading person-heading">Zu meiner Person</h2>
  <p class="block bio">Ich bin <strong>Malte Ewald Krings</strong>, Transaktionsanalytiker,<br>psychotherapeutischer Heilpraktiker und begeis-<br>terter Anwender der Vitalen Integrations-<br>Methode VIM®.</p>
  <div class="portrait" role="img" aria-label="Porträtfoto von Malte Ewald Krings im hellblauen Hemd vor hellem Hintergrund"></div>

  <svg class="quote-mark" width="36" height="36" viewBox="0 0 36 36" aria-hidden="true">
    <circle cx="18" cy="18" r="18" fill="var(--quote-dot)"/>
    <path d="M13.5 13 L10 23 M20.5 13 L17 23" stroke="#ffffff" stroke-width="2.6" stroke-linecap="round"/>
  </svg>
  <blockquote class="block quote">Bei aller Ernsthaftigkeit und Empa-<br>thie dürfen Leichtigkeit, Zuversicht<br>und Humor in der Beratung nicht zu<br>kurz kommen.</blockquote>

  <div class="rule rule-right-1"></div>

  <h2 class="block section-heading services-heading">Mein Leistungsspektrum für Sie</h2>
  <ul class="block services">
    <li>Effektive Kurztherapie</li>
    <li>Coaching zu beruflichen Anliegen</li>
    <li>Auftrittscoaching - Mentales Training</li>
    <li>Entlastung in akuten Krisen</li>
  </ul>

  <div class="rule rule-right-2"></div>

  <h2 class="block section-heading methods-heading">Angewandte Methoden</h2>

  <section class="methods-box">
    <article class="method method-ta">
      <h3>Transaktionsanalyse</h3>
      <p>Die TA ist eine Theorie<br>der Persönlichkeit, die<br>menschliches Verhalten<br>verständlich erklärt.<br>Das zentrale Anliegen<br>transaktionsanalytischer<br>Beratung ist es, KlientIn-<br>nen darin zu unterstüt-<br>zen, ihre gewohnte Sicht<br>der Wirklichkeit, deren<br>Deutung und die damit<br>verbundenen Verhal-<br>tensweisen zu erwei-<br>tern. Hierbei kann jeder<br>Mensch bei entspre-<br>chender Förderung und<br>Unterstützung selbst<br>herausfinden kann, was<br>für ihn/sie richtig ist.</p>
    </article>
    <div class="method-divider"></div>
    <article class="method method-vim">
      <h3>VIM®</h3>
      <p>Die Vitale Integra-<br>tions-Methode (VIM®)<br>wurde zunächst als<br>Zusatztechnik ent-<br>wickelt, mittlerweile<br>hat sie sich zu einer<br>eigenständigen<br>Verfahren weiterent-<br>wickelt. Kurz: VIM® ein<br>Verfahren, um aktuell<br>belastende Gefühle<br>(wie Angst oder Stress)<br>zu behandeln und<br>damit zusammenhän-<br>gende Überzeugungen<br>zu verändern. Sie ist zu-<br>dem eine hervorragen-<br>de Selbsthilfetechnik<br>für die Klienten.</p>
    </article>
  </section>
</main>
</body>
</html>
```